Brackenford Fluidworks needs a website describing the repair business we are in.

Brackenford Fluidworks is a full hydraulic repair facility. We have 2 shops. We repair and service all hydraulic cylinders, pneumatic cylinders, hydraulic pumps, motors, valves and gearboxes. Our services range from large industrial plants to the individual that owns one piece of equipment. We also offer removal and install of cylinders. Along with free pick up and delivery, within a certain distance which is usually 100 miles from one of our shops.

With over 30 years experience in the hydraulic business, we can repair or replace any job. There is not a job too big or too small, we service them all.

We have customers that send whole pieces of equipment to us to do complete overhauls on all the hydraulics. Ranging from a country club green roller to a 10 ton boom truck.

Target Market(s)

Industrial plants, road builders, dirt work companies, general contractors, owners of industrial equipment (bulldozers, excavators, loaders, scrapers, motor graders, etc.

Industry/Entity Type

Hydraulic

Number of Pages Required

5+ page

Font styles to use
Sans Serif

Colors
ec1f27
ffffff
aaaaaa

Requirements
Must have
• Information about what we offer and pictures of jobs completed.
Nice to have
• Nice stock photos of jobsites and industrial plants.
Should not have
• Any sort of comical characters.

```html
<!DOCTYPE html>
<html lang="en">
<head>
<meta charset="utf-8">
<title>Brackenford Fluidworks — Hydraulic Repair</title>
<link rel="stylesheet" href="https://fonts.googleapis.com/css2?family=Roboto:wght@400;500;700;900&family=Open+Sans:ital,wght@0,400;0,600;0,700;1,400&display=swap">
<style>
:root{
  --red:#ec1f27;
  --white:#ffffff;
  --grey:#aaaaaa;
  --ink:#1d1d1d;
  --text:#555555;
  --footer:#1b1b1b;
  --rule:#dddddd;
}
*{box-sizing:border-box;margin:0;padding:0}
html,body{width:1200px;height:2748px;overflow:hidden;background:var(--white)}
body{position:relative;font-family:"Open Sans",Arial,sans-serif;color:var(--text)}
.abs{position:absolute}

/* header */
.topbar{position:absolute;left:636px;top:0;width:564px;height:36px;background:var(--red);clip-path:polygon(0 0,100% 0,100% 100%,34px 100%);color:var(--white);font:600 15px "Open Sans",sans-serif;display:flex;align-items:center;gap:20px;padding-left:62px}
.topbar svg{vertical-align:-2px;margin-right:8px}
.topbar .sep{opacity:.7}
.header{position:absolute;left:0;top:0;width:1200px;height:92px;z-index:1}
.header-rule{position:absolute;left:0;top:0;width:640px;height:4px;background:var(--red)}
.brand-badge{position:absolute;left:92px;top:-12px;width:184px;height:184px;border-radius:50%;background:var(--white);z-index:3;display:flex;align-items:center;justify-content:center;text-align:center;padding:38px 20px 0}
.brand-name{font:700 22px/1.1 "Roboto",sans-serif;color:var(--red);text-transform:uppercase}
.nav{position:absolute;right:82px;top:56px;display:flex;gap:34px;font:500 15px "Roboto",sans-serif;color:var(--ink);text-transform:uppercase;z-index:2}
.nav .active{color:var(--red)}

/* hero */
.hero{position:absolute;left:0;top:92px;width:1200px;height:516px;background:linear-gradient(180deg,#2f4a6e 0%,#5d7fa6 38%,#3a4e6a 58%,#b4743e 72%,#253346 86%,#1b2433 100%);text-align:center;color:var(--white)}
.hero-title{position:absolute;left:0;width:100%;top:142px;font:700 66px "Roboto",sans-serif;text-transform:uppercase;letter-spacing:.5px}
.hero-sub{position:absolute;left:0;width:100%;top:228px;font:400 27px "Open Sans",sans-serif}
.hero-btn{position:absolute;left:500px;top:285px;width:200px;height:55px;border:2px solid var(--white);border-radius:28px;font:700 17px/51px "Roboto",sans-serif;text-transform:uppercase}
.dots{position:absolute;left:0;width:100%;top:434px;display:flex;justify-content:center;gap:5px}
.dots span{width:13px;height:13px;border-radius:50%;border:2px solid var(--white)}
.dots .on{background:var(--white)}

/* welcome */
.section-title{position:absolute;left:0;width:1200px;text-align:center;font:700 34px "Roboto",sans-serif;color:var(--ink);text-transform:uppercase}
.intro{position:absolute;left:220px;width:760px;top:738px;text-align:center;font:400 14px/27px "Open Sans",sans-serif}
.feature{position:absolute;top:814px;width:240px;text-align:center}
.feature-ring{width:150px;height:150px;margin:0 auto;border-radius:50%;border:2px solid var(--grey);display:flex;align-items:center;justify-content:center}
.feature-ring span{width:134px;height:134px;border-radius:50%;border:6px solid var(--grey);display:flex;align-items:center;justify-content:center;background:var(--white)}
.feature-title{margin-top:26px;font:500 20px "Roboto",sans-serif;color:var(--ink)}
.feature-text{margin-top:12px;font:400 14px/24px "Open Sans",sans-serif}
.read-more{margin-top:12px;font:700 14px "Open Sans",sans-serif;color:var(--red);text-transform:uppercase}

/* what we do */
.what{position:absolute;left:0;top:1189px;width:1200px;height:425px;background:linear-gradient(135deg,#6d6d6d 0%,#575757 45%,#4a4a4a 100%)}
.what-bg{position:absolute;inset:0}
.what-title{position:absolute;left:101px;top:52px;font:700 31px "Roboto",sans-serif;color:var(--white);text-transform:uppercase}
.what-text{position:absolute;left:101px;top:108px;width:470px;font:400 14px/27px "Open Sans",sans-serif;color:#eeeeee}
.what-text p+p{margin-top:20px}
.btn-red{position:absolute;left:99px;top:322px;width:132px;height:41px;border-radius:21px;background:var(--red);color:var(--white);font:700 14px/41px "Open Sans",sans-serif;text-align:center;text-transform:uppercase}
.video{position:absolute;left:636px;top:60px;width:464px;height:305px;border:4px solid var(--white);background:linear-gradient(180deg,#6a6058 0%,#8a8f96 55%,#7a6a55 100%)}
.play{position:absolute;left:204px;top:123px;width:50px;height:50px}

/* blog */
.card{position:absolute;top:1770px;width:321px}
.card-photo{width:321px;height:212px}
.date{position:absolute;left:-7px;top:139px;width:44px;height:60px;background:var(--red);color:var(--white);text-align:center;padding-top:6px}
.date b{display:block;font:700 24px/26px "Roboto",sans-serif}
.date small{display:block;font:400 12px "Open Sans",sans-serif;text-transform:uppercase}
.card-title{margin-top:36px;font:600 18px/24px "Open Sans",sans-serif;color:var(--ink)}
.card-text{margin-top:8px;font:400 13px/22px "Open Sans",sans-serif;color:#666}
.card-rule{margin-top:10px;height:1px;background:var(--rule)}
.card-author{margin-top:12px;font:400 12px "Open Sans",sans-serif;color:#666;display:flex;align-items:center;gap:8px}

/* testimonial */
.quote-band{position:absolute;left:0;top:2235px;width:888px;height:143px;background:var(--red);clip-path:polygon(0 0,824px 0,888px 100%,0 100%)}
.avatar{position:absolute;left:99px;top:19px;width:102px;height:102px;border-radius:50%;border:4px solid var(--white);background:linear-gradient(180deg,#b8a89a,#6d7e92)}
.quote-rule{position:absolute;left:227px;top:26px;width:1px;height:92px;background:rgba(255,255,255,.6)}
.quote{position:absolute;left:255px;top:30px;width:520px;font:italic 400 14px/22px "Open Sans",sans-serif;color:var(--white)}
.quote-name{position:absolute;left:255px;top:85px;font:400 19px "Open Sans",sans-serif;color:var(--white)}
.arrows{position:absolute;left:791px;top:101px;display:flex;gap:4px}

/* footer */
.footer{position:absolute;left:0;top:2378px;width:1200px;height:370px;background:var(--footer);color:#dddddd}
.footer-brand{position:absolute;left:100px;top:72px;width:200px;display:flex;flex-direction:column;align-items:center;gap:14px}
.footer-brand .mark{width:84px;height:84px;border-radius:50%;background:var(--red)}
.footer-brand .name{font:700 24px/1.1 "Roboto",sans-serif;color:var(--red);text-align:center;text-transform:uppercase}
.col-title{position:absolute;top:70px;font:500 20px "Roboto",sans-serif;color:var(--white)}
.links{position:absolute;left:403px;top:106px;list-style:none;font:400 13px/25px "Open Sans",sans-serif}
.news-text{position:absolute;left:577px;top:106px;width:250px;font:400 13px/22px "Open Sans",sans-serif}
.news-input{position:absolute;left:577px;top:165px;width:253px;height:35px;background:var(--white);color:#666;font:400 12px/35px "Open Sans",sans-serif;padding-left:14px}
.news-btn{position:absolute;left:577px;top:218px;width:101px;height:33px;border-radius:17px;background:var(--red);color:var(--white);font:600 12px/33px "Open Sans",sans-serif;text-align:center;text-transform:uppercase}
.contact{position:absolute;left:898px;top:106px;list-style:none;font:400 13px/22px "Open Sans",sans-serif}
.contact li{display:flex;gap:18px;margin-bottom:18px}
.contact svg{flex:none;margin-top:4px}
.footer-rule{position:absolute;left:99px;top:293px;width:1002px;height:1px;background:#3a3a3a}
.copyright{position:absolute;left:99px;top:320px;font:400 12px "Open Sans",sans-serif}
.social{position:absolute;left:965px;top:314px;display:flex;gap:6px}
.social span{width:30px;height:30px;border-radius:50%;border:1.5px solid #cccccc}
</style>
</head>
<body>

<header class="header">
  <div class="header-rule"></div>
  <div class="brand-badge"><span class="brand-name">Brackenford Fluidworks</span></div>
  <nav class="nav">
    <span class="active">Home</span><span>About Us</span><span>Services</span><span>Projects</span><span>Blog</span><span>Contact Us</span>
    <svg width="16" height="16" viewBox="0 0 16 16"><circle cx="6.5" cy="6.5" r="5" fill="none" stroke="#1d1d1d" stroke-width="2.2"/><line x1="10.3" y1="10.3" x2="15" y2="15" stroke="#1d1d1d" stroke-width="2.6"/></svg>
  </nav>
</header>
<div class="topbar">
  <span><svg width="14" height="14" viewBox="0 0 24 24"><path fill="#fff" d="M6.6 10.8a15.1 15.1 0 0 0 6.6 6.6l2.2-2.2c.3-.3.7-.4 1-.2 1.1.4 2.3.6 3.6.6.6 0 1 .4 1 1V20c0 .6-.4 1-1 1A17 17 0 0 1 3 4c0-.6.4-1 1-1h3.5c.6 0 1 .4 1 1 0 1.3.2 2.5.6 3.6.1.3 0 .7-.2 1z"/></svg>1 800 555 0142</span>
  <span class="sep">|</span>
  <span><svg width="15" height="12" viewBox="0 0 20 16"><rect width="20" height="16" rx="2" fill="#fff"/><path d="M1 2l9 7 9-7" fill="none" stroke="#ec1f27" stroke-width="2"/></svg>info@brackenfordfluidworks.com</span>
</div>

<section class="hero" role="img" aria-label="Industrial power plant with cooling towers lit at dusk, reflected in water">
  <h1 class="hero-title">Brackenford Fluidworks</h1>
  <p class="hero-sub">Brackenford Fluidworks is a full hydraulic repair facility</p>
  <div class="hero-btn">Get More Info</div>
  <div class="dots"><span class="on"></span><span></span><span></span><span></span></div>
</section>

<h2 class="section-title" style="top:678px">Welcome to Brackenford Fluidworks</h2>
<p class="intro">Nam libero tempore, cum soluta nobis est eligendi optio cumque nihil impedit quo minus id quod maxime placeat facere possimus, omnis voluptas assumenda est, omnis dolor repelle s autem quibusdam et aut officiis debitisa</p>

<div class="feature" style="left:87px">
  <div class="feature-ring"><span>
    <svg width="60" height="60" viewBox="0 0 60 60" fill="#ec1f27"><circle cx="22" cy="34" r="13"/><circle cx="22" cy="34" r="5" fill="#fff"/><g stroke="#ec1f27" stroke-width="6"><line x1="22" y1="16" x2="22" y2="52"/><line x1="4" y1="34" x2="40" y2="34"/><line x1="9" y1="21" x2="35" y2="47"/><line x1="9" y1="47" x2="35" y2="21"/></g><circle cx="22" cy="34" r="5" fill="#fff"/><circle cx="45" cy="15" r="8"/><circle cx="45" cy="15" r="3" fill="#fff"/><circle cx="47" cy="42" r="6"/><circle cx="47" cy="42" r="2.2" fill="#fff"/></svg>
  </span></div>
  <div class="feature-title">Installation</div>
  <div class="feature-text">At vero eos est accusamus et ius<br>to odio dnissimos ducim</div>
  <div class="read-more">Read More</div>
</div>
<div class="feature" style="left:349px">
  <div class="feature-ring"><span>
    <svg width="56" height="56" viewBox="0 0 56 56"><path fill="#ec1f27" d="M47 6a13 13 0 0 0-16 16L6 47a4.5 4.5 0 0 0 6 6l25-25a13 13 0 0 0 16-16l-8 8-7-2-2-7z"/><circle cx="10" cy="49" r="2" fill="#fff"/></svg>
  </span></div>
  <div class="feature-title">Repair or Replace</div>
  <div class="feature-text">At vero eos est accusamus et ius<br>to odio dnissimos ducim</div>
  <div class="read-more">Read More</div>
</div>
<div class="feature" style="left:609px">
  <div class="feature-ring"><span>
    <svg width="52" height="52" viewBox="0 0 52 52"><polygon fill="#ec1f27" points="26,2 31,9 39,5 40,14 49,14 45,22 51,28 43,32 46,41 37,41 35,50 27,45 20,51 16,43 7,44 9,35 1,30 8,24 4,16 13,14 13,5 21,9"/></svg>
  </span></div>
  <div class="feature-title">30 years experience</div>
  <div class="feature-text">At vero eos est accusamus et ius<br>to odio dnissimos ducim</div>
  <div class="read-more">Read More</div>
</div>
<div class="feature" style="left:871px">
  <div class="feature-ring"><span>
    <svg width="58" height="44" viewBox="0 0 58 44"><rect x="0" y="0" width="58" height="44" rx="8" fill="#ec1f27"/><rect x="8" y="10" width="26" height="18" fill="#fff"/><path d="M36 16h8l6 7v5H36z" fill="#fff"/><circle cx="16" cy="32" r="4" fill="#fff"/><circle cx="42" cy="32" r="4" fill="#fff"/></svg>
  </span></div>
  <div class="feature-title">Pick up &amp; Delivery</div>
  <div class="feature-text">At vero eos est accusamus et ius<br>to odio dnissimos ducim</div>
  <div class="read-more">Read More</div>
</div>

<section class="what">
  <div class="what-bg" role="img" aria-label="Muted workshop yard with trucks, shown behind a grey overlay"></div>
  <h2 class="what-title">What We Do</h2>
  <div class="what-text">
    <p>Nam libero tempore, cum soluta nobis est eligendi optio cumque nihil impedit quo minus id quod maxim.</p>
    <p>Paceat facere possimus, omnis voluptas assumenda est, omnsdolor repellendus. Temporibus autem quibusdam et aut officiis debitiaut rerum necessitatibus saepe eveniet ut et voluptates repudiandasint et molestiae non recusanda. earum rer.</p>
  </div>
  <div class="btn-red">Read More</div>
  <div class="video" role="img" aria-label="Video still of two repaired hydraulic cylinders on wooden pallets in the shop">
    <svg class="play" viewBox="0 0 50 50"><circle cx="25" cy="25" r="25" fill="#1a1a1a"/><polygon points="19,14 37,25 19,36" fill="#fff"/></svg>
  </div>
</section>

<h2 class="section-title" style="top:1694px">Latest Blog</h2>

<article class="card" style="left:97px">
  <div class="card-photo" role="img" aria-label="Black hydraulic cylinders laid out on a workshop floor" style="background:linear-gradient(160deg,#55585c,#2b2c2f 60%,#77787a)"></div>
  <div class="date"><b>04</b><small>Sep</small></div>
  <h3 class="card-title">At vero eos et accusamus et iustoer odio dignissimos duci</h3>
  <p class="card-text">At vero eos et accusamus et iusto odio dignissimodu cimus qui blanditiis praesentium volup</p>
  <div class="card-rule"></div>
  <div class="card-author"><svg width="11" height="12" viewBox="0 0 11 12"><circle cx="5.5" cy="3" r="3" fill="#ec1f27"/><path d="M0 12a5.5 5 0 0 1 11 0z" fill="#ec1f27"/></svg>Maren Holt</div>
</article>
<article class="card" style="left:441px">
  <div class="card-photo" role="img" aria-label="Red painted hydraulic cylinders on a shop bench" style="background:linear-gradient(160deg,#5a4a40,#a8503e 50%,#6b5d50)"></div>
  <div class="date"><b>30</b><small>Aug</small></div>
  <h3 class="card-title">At vero eos et accusamus et iustoer odio dignissimos duci</h3>
  <p class="card-text">At vero eos et accusamus et iusto odio dignissimodu cimus qui blanditiis praesentium volup</p>
  <div class="card-rule"></div>
  <div class="card-author"><svg width="11" height="12" viewBox="0 0 11 12"><circle cx="5.5" cy="3" r="3" fill="#ec1f27"/><path d="M0 12a5.5 5 0 0 1 11 0z" fill="#ec1f27"/></svg>Maren Holt</div>
</article>
<article class="card" style="left:784px">
  <div class="card-photo" role="img" aria-label="Blue hydraulic pump on a wooden pallet in a truck bed" style="background:linear-gradient(160deg,#3a3836,#8a7356 55%,#2f2e2d)"></div>
  <div class="date"><b>08</b><small>Sep</small></div>
  <h3 class="card-title">At vero eos et accusamus et iustoer odio dignissimos duci</h3>
  <p class="card-text">At vero eos et accusamus et iusto odio dignissimodu cimus qui blanditiis praesentium volup</p>
  <div class="card-rule"></div>
  <div class="card-author"><svg width="11" height="12" viewBox="0 0 11 12"><circle cx="5.5" cy="3" r="3" fill="#ec1f27"/><path d="M0 12a5.5 5 0 0 1 11 0z" fill="#ec1f27"/></svg>Maren Holt</div>
</article>

<section class="quote-band">
  <div class="avatar" role="img" aria-label="Portrait photo of the client quoted"></div>
  <div class="quote-rule"></div>
  <p class="quote">" Nam libero tempore, cum soluta nobis est eligendi optio cumque nihil impedit quo minus id quod maxime placeat facere possimus, om."</p>
  <p class="quote-name">- Dorian Vasquel</p>
  <div class="arrows">
    <svg width="18" height="18" viewBox="0 0 18 18"><circle cx="9" cy="9" r="9" fill="#fff"/><path d="M11 4l-5 5 5 5" fill="none" stroke="#ec1f27" stroke-width="2.4"/></svg>
    <svg width="18" height="18" viewBox="0 0 18 18"><circle cx="9" cy="9" r="9" fill="#fff"/><path d="M7 4l5 5-5 5" fill="none" stroke="#ec1f27" stroke-width="2.4"/></svg>
  </div>
</section>

<footer class="footer">
  <div class="footer-brand"><span class="mark"></span><span class="name">Brackenford Fluidworks</span></div>

  <h4 class="col-title" style="left:403px">Information</h4>
  <ul class="links"><li>Help</li><li>FAQ</li><li>Support</li><li>Sitemap</li><li>Terms Of Use</li><li>Privacy Statement</li></ul>

  <h4 class="col-title" style="left:577px">Newsletter Subscription</h4>
  <p class="news-text">Register your Email Address to get Information about us</p>
  <div class="news-input">Email Address</div>
  <div class="news-btn">Subscribe</div>

  <h4 class="col-title" style="left:898px">Contact Us</h4>
  <ul class="contact">
    <li><svg width="11" height="15" viewBox="0 0 11 15"><path d="M5.5 0A5.5 5.5 0 0 0 0 5.5C0 9.6 5.5 15 5.5 15S11 9.6 11 5.5A5.5 5.5 0 0 0 5.5 0z" fill="#fff"/><circle cx="5.5" cy="5.5" r="2" fill="#1b1b1b"/></svg><span>P.O Box 214, Millbrook Yard<br>Harlow Ridge</span></li>
    <li style="margin-top:10px"><svg width="13" height="13" viewBox="0 0 24 24"><path fill="#fff" d="M6.6 10.8a15.1 15.1 0 0 0 6.6 6.6l2.2-2.2c.3-.3.7-.4 1-.2 1.1.4 2.3.6 3.6.6.6 0 1 .4 1 1V20c0 .6-.4 1-1 1A17 17 0 0 1 3 4c0-.6.4-1 1-1h3.5c.6 0 1 .4 1 1 0 1.3.2 2.5.6 3.6.1.3 0 .7-.2 1z"/></svg><span>1-800 555 0142</span></li>
    <li style="margin-top:22px"><svg width="14" height="11" viewBox="0 0 20 16"><rect width="20" height="16" rx="2" fill="#fff"/><path d="M1 2l9 7 9-7" fill="none" stroke="#1b1b1b" stroke-width="2"/></svg><span>info@brackenfordfluidworks.com</span></li>
  </ul>

  <div class="footer-rule"></div>
  <p class="copyright">Copyrights © 2018, Brackenford Fluidworks. All rights reserved.</p>
  <div class="social"><span></span><span></span><span></span><span></span></div>
</footer>

</body>
</html>
```